Business Card for premium dental clinic

We are a premium dental clinic based in Brasov, Romania with more than 15 year on the market, providing quality dental treatment made by a team of more specialized dentists, working with modern equipment as a solution to beautiful and healthy teeth.

Our current logo for the clinic use 2 square with colors black and gold - dr Ternisu - studio, using family fonts Bodoni, Myriad Pro and Segoe Print.
Depending on the printing we used some gold CMYK background or gold foil picture background or a gold gradient.
We want a business card:
- eye catching business card
- distinguished business card
- premium design
- to keep the color scheme of black and gold
- to attract the customers to spent time reading the information
- modern concept

```html
<!DOCTYPE html>
<html lang="en">
<head>
<meta charset="utf-8">
<title>dr Ternisu studio – business card</title>
<link href="https://fonts.googleapis.com/css2?family=Lato:wght@400;700&display=swap" rel="stylesheet">
<style>
  :root {
    --backdrop: #2b2623;
    --card: #141414;
    --card-edge: #1c1c1c;
    --gold: #c3952e;
    --text-light: #c9c9c9;
    --text-muted: #9a9a9a;
    --divider: #4a4a4a;
  }
  * { margin: 0; padding: 0; box-sizing: border-box; }
  html, body {
    width: 1200px; height: 844px; overflow: hidden;
    background: var(--backdrop);
    font-family: "Lato", Arial, sans-serif;
  }
  .sheet {
    width: 1200px; height: 844px;
    display: flex; align-items: center; justify-content: center; gap: 44px;
  }
  .card {
    position: relative;
    width: 520px; height: 300px;
    background: var(--card);
    border: 1px solid var(--card-edge);
    box-shadow: 0 10px 30px rgba(0,0,0,.45);
  }
  .brand {
    position: absolute;
    display: flex; align-items: center; gap: 14px;
  }
  .brand__square {
    width: 46px; height: 46px; background: var(--gold);
  }
  .brand__name {
    font-weight: 700; font-size: 30px; color: var(--gold);
    letter-spacing: .5px; white-space: nowrap;
  }
  .card--front .brand { left: 150px; top: 62px; }
  .card--back .brand { left: 50%; top: 50%; transform: translate(-50%, -50%); }

  .person {
    position: absolute; right: 260px; top: 168px; text-align: left;
  }
  .person__name {
    font-weight: 700; font-size: 17px; color: var(--gold);
    letter-spacing: .3px; white-space: nowrap;
  }
  .person__role {
    font-size: 15px; color: var(--text-muted); margin-top: 1px; white-space: nowrap;
  }
  .divider {
    position: absolute; left: 270px; top: 150px;
    width: 1px; height: 64px; background: var(--divider);
  }
  .contacts {
    position: absolute; left: 284px; top: 150px;
    list-style: none;
  }
  .contacts li {
    display: flex; align-items: center; gap: 8px;
    font-size: 14.5px; color: var(--text-light); line-height: 21px; white-space: nowrap;
  }
  .contacts svg { width: 12px; height: 12px; fill: var(--gold); flex: none; }
  .address {
    position: absolute; left: 168px; top: 246px;
    font-size: 15px; color: var(--text-muted); white-space: nowrap;
  }
</style>
</head>
<body>
<main class="sheet">
  <section class="card card--front" aria-label="Business card front">
    <div class="brand">
      <span class="brand__square"></span>
      <span class="brand__name">dr Ternisu studio</span>
    </div>

    <div class="person">
      <p class="person__name">JONATHAN SMITH</p>
      <p class="person__role">Managing Director</p>
    </div>

    <span class="divider"></span>

    <ul class="contacts">
      <li>
        <svg viewBox="0 0 24 24" aria-hidden="true"><path d="M6.6 10.8a15 15 0 0 0 6.6 6.6l2.2-2.2c.3-.3.7-.4 1-.2 1.1.4 2.3.6 3.6.6.6 0 1 .4 1 1V20c0 .6-.4 1-1 1A17 17 0 0 1 3 4c0-.6.4-1 1-1h3.5c.6 0 1 .4 1 1 0 1.3.2 2.5.6 3.6.1.3 0 .7-.2 1z"/></svg>
        044-123 456 789
      </li>
      <li>
        <svg viewBox="0 0 24 24" aria-hidden="true"><path d="M2 5h20v14H2z M2 5l10 7 10-7" fill="none" stroke="#c3952e" stroke-width="0"/><path d="M2 6.5V19h20V6.5l-10 7z"/><path d="M2 5h20l-10 7z"/></svg>
        info@webname.com
      </li>
      <li>
        <svg viewBox="0 0 24 24" aria-hidden="true"><circle cx="12" cy="12" r="10"/><path d="M2 12h20M12 2c3 3 3 17 0 20M12 2c-3 3-3 17 0 20" stroke="#141414" stroke-width="1.6" fill="none"/></svg>
        www.websitename.com
      </li>
    </ul>

    <p class="address">421, Address line goes here, 45452,Country Name</p>
  </section>

  <section class="card card--back" aria-label="Business card back">
    <div class="brand">
      <span class="brand__square"></span>
      <span class="brand__name">dr Ternisu studio</span>
    </div>
  </section>
</main>
</body>
</html>
```